Vigil Ledger Suite (Web Design)

Design with your logo. Background in black or dark. Elegant style, it's a website for professional people only. Our company provides a cloud software manager for Funeral Services Companies.

Target Market(s)

Professional of Funeral Services.

Coding

Coded - Design and coding required

Number of Pages Required

3 page

Font styles to use
Sans Serif

Colors
fbee3d
000000
5c5c5c

Requirements
Must have
• Design of the website should be similar to our logo colors.

```html
<!DOCTYPE html>
<html lang="en">
<head>
<meta charset="utf-8">
<title>Vigil Ledger Suite</title>
<link href="https://fonts.googleapis.com/css2?family=Arimo:wght@400;700&family=Open+Sans:wght@400;600&display=swap" rel="stylesheet">
<style>
:root{
  --yellow:#fbee3d;
  --gold:#f5cf0c;
  --black:#000000;
  --ink:#1d1d1d;
  --grey:#5c5c5c;
  --dark:#2e2e2e;
  --darker:#1c1c1c;
  --white:#ffffff;
  --muted:#555555;
}
*{margin:0;padding:0;box-sizing:border-box}
html,body{width:1200px;height:3377px;overflow:hidden;background:var(--white)}
body{position:relative;font-family:"Open Sans",Arial,sans-serif;color:var(--ink)}
.abs{position:absolute}
.head-font{font-family:"Arimo",Arial,sans-serif}
.btn{position:absolute;display:flex;align-items:center;justify-content:center;background:var(--gold);color:var(--black);font-family:"Arimo",Arial,sans-serif;font-weight:700;font-size:18px;z-index:2}

/* header */
.site-header{top:0;left:0;width:1200px;height:130px;background:var(--white)}
.brand{left:168px;top:42px;display:flex;align-items:center;gap:12px;font-family:"Arimo",Arial,sans-serif;font-weight:700;font-size:27px;color:var(--gold)}
.brand-dot{width:22px;height:22px;border-radius:50%;background:var(--gold)}
.top-contact{top:24px;left:626px;display:flex;gap:28px;font-size:17px;color:var(--grey)}
.top-contact span{display:flex;align-items:center;gap:8px}
.top-contact .phone{font-weight:600;color:var(--ink);font-size:18px}
.nav-band{top:70px;left:430px;width:770px;height:60px}
.main-nav{top:92px;left:488px;display:flex;gap:22px;font-family:"Arimo",Arial,sans-serif;font-weight:700;font-size:15px;color:var(--ink)}

/* hero */
.hero{top:130px;left:0;width:1200px;height:575px;background:linear-gradient(100deg,#262626 0%,#3c3c3c 45%,#6a6a6a 70%,#4a4a4a 100%)}
.hero-title{left:148px;top:308px;font-weight:700;font-size:38px;color:var(--white)}
.hero-sub{left:148px;top:350px;font-weight:700;font-size:28px;color:var(--white)}
.hero-text{left:152px;top:400px;font-size:20px;line-height:26px;color:var(--white);width:420px}
.hero-dots{top:654px;left:566px;display:flex;gap:10px}
.dot{width:17px;height:17px;border-radius:50%;border:2px solid #d9d9d9}
.dot.on{background:#d9d9d9}

/* about */
.about-media{top:793px;left:150px;width:470px;height:302px;background:linear-gradient(135deg,#b9bff0,#8f98dc)}
.play{left:345px;top:910px;width:76px;height:76px;border-radius:50%;background:var(--white)}
.section-title{font-weight:700;font-size:34px;color:var(--ink)}
.about-title{left:668px;top:795px}
.about-lead{left:671px;top:850px;width:430px;font-size:19px;line-height:26px;color:var(--ink)}
.about-body{left:670px;top:918px;width:420px;font-size:14px;line-height:23px;color:var(--ink)}

/* services */
.services-band{top:1170px;left:0;width:1200px;height:560px}
.services-title{top:1248px;left:0;width:1200px;text-align:center;font-size:30px}
.card{position:absolute;top:1345px;width:208px;height:265px;border:2px solid var(--ink);text-align:center}
.card.featured{background:var(--white);border-color:var(--white)}
.card-icon{position:absolute;left:76px;top:-22px;width:56px;height:56px;border-radius:50%;background:var(--white);border:2px solid var(--ink)}
.card h3{margin-top:80px;font-family:"Arimo",Arial,sans-serif;font-size:17px;line-height:19px;color:var(--black)}
.card p{margin:10px auto 0;width:170px;font-size:13px;line-height:17px;color:var(--ink)}
.card .btn{left:38px;top:200px;width:130px;height:32px;font-size:12px;background:var(--grey);color:var(--white)}
.card.featured .btn{background:var(--gold);color:var(--black)}

/* why */
.laptop-art{left:700px;top:1765px;width:425px;height:310px;background:radial-gradient(ellipse at 55% 50%,#d9d9d9 0%,#f2f2f2 55%,#ffffff 75%);z-index:0}
.why-title{left:176px;top:1810px;font-size:31px;z-index:2}
.why-text{left:176px;top:1868px;width:450px;font-size:14px;line-height:24px;z-index:2}

/* testimonials & contact */
.dark-zone{top:2140px;left:0;width:1200px;height:1095px}
.testi-title{top:2262px;left:0;width:1200px;text-align:center;font-size:30px;color:var(--white)}
.quote-mark{top:2318px;left:0;width:1200px;text-align:center;font-family:"Arimo",Arial,sans-serif;font-weight:700;font-size:70px;color:var(--white)}
.testi-text{top:2384px;left:230px;width:740px;text-align:center;font-size:19px;line-height:27px;color:var(--white)}
.testi-author{top:2488px;left:0;width:1200px;text-align:center;font-size:20px;color:var(--gold)}
.testi-dots{top:2564px;left:573px;display:flex;gap:6px}
.testi-dots .dot{width:14px;height:14px;border-color:var(--gold)}
.testi-dots .dot.on{background:var(--gold)}

.contact-form{top:2752px;left:170px;width:420px;height:396px;background:linear-gradient(180deg,var(--gold),#f7d21a)}
.field{position:absolute;left:42px;width:336px;border-bottom:2px solid var(--ink);font-size:15px;padding-bottom:6px;color:var(--black)}
.submit{left:42px;top:316px;width:168px;height:46px;background:var(--dark);color:var(--white)}
.contact-title{left:688px;top:2776px;font-weight:700;font-size:31px;color:var(--white)}
.contact-info{left:690px;top:2832px;font-size:17px;line-height:24px;color:var(--white)}
.contact-info dt{font-weight:600;font-size:16px}
.contact-info dd{margin-bottom:24px}
.social{left:690px;top:3098px;display:flex;gap:30px}
.social span{width:26px;height:26px;border-radius:50%;border:2px solid var(--white)}

/* footer */
.site-footer{top:3235px;left:0;width:1200px;height:142px;background:var(--white)}
.foot-nav{top:3272px;left:0;width:1200px;display:flex;justify-content:center;gap:22px;font-size:15px;color:var(--ink)}
.copyright{top:3308px;left:0;width:1200px;text-align:center;font-size:13px;color:var(--ink)}
</style>
</head>
<body>

<header class="abs site-header">
  <div class="abs brand"><span class="brand-dot"></span>Vigil Ledger Suite</div>
  <div class="abs top-contact">
    <span><svg width="20" height="14" viewBox="0 0 20 14"><rect width="20" height="14" rx="1" fill="#f5cf0c"/><path d="M1 1l9 7 9-7" stroke="#fff" stroke-width="1.6" fill="none"/></svg>hello@vigilledger.example</span>
    <span class="phone"><svg width="16" height="16" viewBox="0 0 16 16"><path d="M3 1l3 3-2 2c1 2 3 4 5 5l2-2 3 3-2 3C6 14 2 10 1 3z" fill="#f5cf0c"/></svg>(555) 014-2278</span>
  </div>
  <svg class="abs nav-band" viewBox="0 0 770 60" width="770" height="60"><path d="M28 0H770V60H0z" fill="#f5cf0c"/></svg>
  <nav class="abs main-nav"><span>ABOUT</span><span>SERVICES</span><span>FEATURES</span><span>NEWS</span><span>GALLERY</span><span>CONTACT US</span></nav>
</header>

<section class="abs hero" role="img" aria-label="Photo of a businessman in a suit resting his head on clasped hands in an office"></section>
<h1 class="abs hero-title head-font">VIGIL LEDGER SUITE</h1>
<p class="abs hero-sub head-font">QUALITY FUNERAL SERVICE</p>
<p class="abs hero-text">Lorem ipsum dolor sit amet consectetuer adipiscing elit Nam cursus Morbi</p>
<a class="btn" style="left:152px;top:472px;width:185px;height:50px">Learn More</a>
<div class="abs hero-dots"><span class="dot"></span><span class="dot on"></span><span class="dot"></span></div>

<section>
  <div class="abs about-media" role="img" aria-label="Video thumbnail illustration of workflow arrows over gears"></div>
  <svg class="abs play" viewBox="0 0 76 76" width="76" height="76"><circle cx="38" cy="38" r="38" fill="#fff"/><path d="M30 24l22 14-22 14z" fill="#111"/></svg>
  <h2 class="abs section-title head-font about-title">ABOUT VLS</h2>
  <p class="abs about-lead">Lorem ipsum dolor sit amet consectetuer adipiscing elit Nam cursus Morbi</p>
  <p class="abs about-body">Accumsan viverra Duis sed tellus et tortor vestibulum gravida Praesent elementum elit at tellus Curabitur metus ipsum luctus eu malesuada ut tincidunt sed diam Donec quis mi sed magna hendrerit accumsan Suspendisse risus nibh</p>
  <a class="btn" style="left:668px;top:1038px;width:185px;height:50px">Learn More</a>
</section>

<section>
  <svg class="abs services-band" viewBox="0 0 1200 560" width="1200" height="560">
    <path d="M0 110C300 20 800 0 1200 40V500C900 560 400 560 0 480z" fill="#fbee3d"/>
    <path d="M700 20C900 0 1080 10 1200 40V60C1080 30 900 20 760 25z" fill="#5c5c5c"/>
    <path d="M0 470C200 520 400 545 560 552C380 556 180 530 0 495z" fill="#5c5c5c"/>
  </svg>
  <h2 class="abs section-title head-font services-title">OUR SERVICES</h2>
  <div class="card featured" style="left:162px"><span class="card-icon"></span><h3>ONLINE<br>SOFTWARE</h3><p>Accumsan viverra Duis sed tellus et tortor vestibulum gravida Praesent</p><a class="btn">Learn More</a></div>
  <div class="card" style="left:385px"><span class="card-icon"></span><h3>PERSONALIZED<br>DOCUMENTS</h3><p>Accumsan viverra Duis sed tellus et tortor vestibulum gravida Praesent</p><a class="btn">Learn More</a></div>
  <div class="card" style="left:608px"><span class="card-icon"></span><h3>SOFTWARE<br>CUSTOMIZATION</h3><p>Accumsan viverra Duis sed tellus et tortor vestibulum gravida Praesent</p><a class="btn">Learn More</a></div>
  <div class="card" style="left:832px"><span class="card-icon"></span><h3>BILLING<br>&amp; ARCHIVING</h3><p>Accumsan viverra Duis sed tellus et tortor vestibulum gravida Praesent</p><a class="btn">Learn More</a></div>
</section>

<section>
  <div class="abs laptop-art" role="img" aria-label="Laptop showing a software dashboard with curved arrows around it"></div>
  <h2 class="abs section-title head-font why-title">WHY CHOOSE VLS</h2>
  <p class="abs why-text">Pellentesque faucibus Ut accumsan ultricies elit Maecenas at justo id velit placerat molestie Donec dictum lectus non odio<br>Cras a ante vitae enim iaculis aliquam Mauris nunc quam venenatis nec euismod sit amet egestas placerat est Pellentesque habitant morbi tristique senectus et netus et malesuada fames ac turpis egestas Cras id elit Integer quis urna Ut</p>
  <a class="btn" style="left:175px;top:2048px;width:185px;height:46px">Learn More</a>
</section>

<svg class="abs dark-zone" viewBox="0 0 1200 1095" width="1200" height="1095" role="img" aria-label="Dark photo backdrop of a worried man at a laptop">
  <defs><linearGradient id="shade" x1="0" y1="0" x2="0" y2="1"><stop offset="0" stop-color="#2a2a2a"/><stop offset="0.5" stop-color="#3a3a3a"/><stop offset="1" stop-color="#262626"/></linearGradient></defs>
  <path d="M0 130C300 40 700 10 1200 30V1095H0z" fill="url(#shade)"/>
  <path d="M0 110C300 20 700 -5 1200 15V35C700 15 300 40 0 135z" fill="#5c5c5c"/>
  <path d="M0 125C100 95 160 80 230 70C150 95 80 115 0 150z" fill="#f5cf0c"/>
  <path d="M760 490C950 470 1100 440 1200 410V440C1080 470 930 490 760 490z" fill="#f5cf0c"/>
  <path d="M0 510C400 480 800 490 1200 430V500H0z" fill="#303030"/>
</svg>
<h2 class="abs section-title head-font testi-title">TESTIMONIALS</h2>
<div class="abs quote-mark">&#8220;</div>
<p class="abs testi-text">Donec quis mi sed magna hendrerit accumsan Suspendisse risus nibh ultricies eu volutpat non condimentum hendrerit augue Etiam eleifend metus vitae adipiscing semper mauris ipsum iaculis elit congue elit mi egestas</p>
<p class="abs testi-author">BY AUTHOR NAME</p>
<div class="abs testi-dots"><span class="dot"></span><span class="dot on"></span><span class="dot"></span></div>

<section>
  <form class="abs contact-form">
    <span class="field" style="top:40px">NAME</span>
    <span class="field" style="top:94px">EMAIL</span>
    <span class="field" style="top:148px">PHONE NUMBER</span>
    <span class="field" style="top:202px;height:80px">MESSAGE</span>
    <a class="btn submit">SUBMIT</a>
  </form>
  <h2 class="abs contact-title head-font">CONTACT US</h2>
  <dl class="abs contact-info">
    <dt>ADDRESS</dt><dd>48 CEDAR ROW, ASHFORD VALE 4021<br>NORTHBRIDGE</dd>
    <dt>PHONE NUMBER</dt><dd>0400 555 318</dd>
    <dt>EMAIL US</dt><dd>CONTACT@VIGILLEDGER.EXAMPLE</dd>
  </dl>
  <div class="abs social"><span></span><span></span><span></span><span></span></div>
</section>

<footer class="abs site-footer"></footer>
<nav class="abs foot-nav"><span>HOME</span><span>ABOUT</span><span>SERVICES</span><span>FEATURES</span><span>NEWS</span><span>GALLERY</span><span>CONTACT US</span></nav>
<p class="abs copyright">© 2019 Vigil Ledger Suite &nbsp;All right reserved</p>

</body>
</html>
```